New iOS App design for Boston Startup

We are looking for a new app design for our iPhone app. The current app's design feels outdated and we like to add lots of new functionality and a new navigation as well. A complete overhaul therefore!
We want you to design 5 screens that will have changed the most. The complete wireframes of these 5 pages are attached in the requirements document.
Once the winning design is selected we will award the winner with the designing all other screens (40-50 screens based on the same design). This will be a separate project worth $1000. The winning designer can get more follow up work if both sides are happy about the cooperation.
We will give feedback as soon as the first screen has been uploaded for review. Final decision will be made only after all 5 screens are finished.
We hope you give it your best!
Note: will only communicate through PixelHarbor (no skype),
Updates
Reason: Want to give designers a chance to submit their designs as I understand from some, the deadline is too close.
I have raised the award and introduced a 2nd price as well to make it worth your time. I hope you give it your best shot.
Reason: A few of you have asked for an extension of the deadline as time is running out. I will extend by one day. Tell me if you need more.
Industry/Entity Type
Startup
Requirements
Must have
- At least 1 screen before we can give you feedback.
Nice to have
- multiple options of 1 screen to get to a desirable design

```html
<!DOCTYPE html>
<html lang="en">
<head>
<meta charset="utf-8">
<title>Home – Daniel Maron</title>
<link href="https://fonts.googleapis.com/css2?family=Arimo:wght@400;700&display=swap" rel="stylesheet">
<style>
  :root {
    --red: #ef5050;
    --green: #45c04f;
    --blue: #3e9be0;
    --orange: #f9b02a;
    --ink: #222;
    --grey: #555;
    --muted: #777;
    --line: #e2e2e2;
    --white: #fff;
    --black: #000;
    --arrow-up: #3fb64a;
  }
  * { box-sizing: border-box; margin: 0; padding: 0; }
  html, body { width: 676px; height: 1200px; overflow: hidden; background: var(--white); }
  body { font-family: "Arimo", Helvetica, Arial, sans-serif; color: var(--ink); }
  .screen { position: relative; width: 640px; height: 1136px; transform: scale(1.05625); transform-origin: 0 0; background: var(--white); overflow: hidden; }
  .abs { position: absolute; }

  .status-bar { left: 0; top: 0; width: 640px; height: 40px; background: var(--black); color: var(--white); font-size: 25px; font-weight: 700; }
  .status-bar .carrier { left: 8px; top: 6px; display: flex; align-items: flex-end; gap: 6px; }
  .status-bar .time { left: 0; width: 640px; top: 6px; text-align: center; }
  .status-bar .indicators { right: 10px; top: 8px; display: flex; gap: 16px; }

  .app-header { left: 0; top: 40px; width: 640px; height: 88px; background: var(--red); color: var(--white); }
  .app-header .menu { left: 24px; top: 28px; }
  .app-header h1 { left: 146px; top: 24px; font-size: 38px; font-weight: 400; letter-spacing: -0.3px; }

  .profile { left: 0; top: 128px; width: 640px; height: 285px; }
  .profile .backdrop { left: 0; top: 0; width: 640px; height: 285px; background: linear-gradient(160deg, #7b8ea8 0%, #a9bcd2 35%, #5e7693 65%, #b6c6d8 100%); }
  .profile .avatar { left: 17px; top: 37px; width: 180px; height: 180px; border-radius: 50%; border: 4px solid var(--white); background: radial-gradient(circle at 50% 40%, #c49a84 0%, #8f6b5a 55%, #d7dbe0 100%); }
  .profile .name { left: 228px; top: 56px; font-size: 40px; font-weight: 700; color: var(--white); }
  .profile .location { left: 228px; top: 104px; font-size: 26px; color: var(--white); display: flex; align-items: center; gap: 8px; }
  .profile .score { left: 228px; top: 162px; color: var(--white); display: flex; align-items: center; }
  .score .label { font-size: 40px; margin-right: 12px; }
  .score .value { font-size: 52px; color: var(--black); }
  .score .delta { font-size: 24px; margin-left: 8px; margin-top: -6px; }

  .stats { left: 0; top: 413px; width: 640px; height: 93px; background: rgba(225, 232, 240, 0.88); display: flex; }
  .stat { height: 93px; padding-top: 10px; }
  .stat + .stat { border-left: 1px solid #5a6470; }
  .stat .figure { font-size: 32px; display: flex; align-items: center; color: var(--ink); }
  .stat .caption { font-size: 26px; color: var(--grey); margin-top: 8px; }
  .stat.this-week { display: flex; align-items: flex-end; padding: 0 0 12px 10px; font-size: 26px; color: var(--grey); }
  .progress { left: 0; top: 507px; width: 497px; height: 10px; background: var(--red); }
  .progress-rest { left: 499px; top: 507px; width: 141px; height: 4px; background: var(--black); }

  .shortcut { width: 180px; height: 180px; border-radius: 50%; border: 4px solid var(--white); box-shadow: 3px 4px 6px rgba(0,0,0,0.55); color: var(--white); font-size: 28px; text-align: center; line-height: 34px; display: flex; flex-direction: column; align-items: center; justify-content: center; }
  .shortcut svg { margin-top: 16px; }
  .shortcut.analytics { left: 20px; top: 563px; background: var(--green); }
  .shortcut.course { left: 232px; top: 563px; background: var(--blue); }
  .shortcut.countdown { left: 443px; top: 563px; background: var(--orange); }

  .divider { left: 0; width: 640px; height: 4px; background: var(--line); }

  .up-next { left: 213px; top: 825px; }
  .up-next .text { left: 0; top: 0; width: 412px; height: 132px; color: var(--white); text-align: center; padding-top: 36px; }
  .up-next .topic { font-size: 26px; }
  .up-next .lesson { font-size: 34px; margin-top: 6px; }

  .tab-bar { left: 0; top: 1009px; width: 640px; height: 127px; display: flex; justify-content: space-around; padding: 14px 6px 0; }
  .tab { width: 102px; height: 103px; display: flex; flex-direction: column; align-items: center; justify-content: flex-end; padding-bottom: 6px; font-size: 20px; color: var(--grey); gap: 8px; }
  .tab.active { background: var(--red); color: var(--white); }
</style>
</head>
<body>
<div class="screen">

  <div class="abs status-bar">
    <div class="abs carrier">
      <svg width="34" height="20" viewBox="0 0 34 20"><rect x="0" y="15" width="4" height="5" fill="#fff"/><rect x="7" y="11" width="4" height="9" fill="#fff"/><rect x="14" y="7" width="4" height="13" fill="#fff"/><rect x="21" y="3" width="4" height="17" fill="#fff"/><rect x="28" y="0" width="4" height="20" fill="#fff"/></svg>
      <span>ORBIT&nbsp;&nbsp;3G</span>
    </div>
    <div class="abs time">9:51 PM</div>
    <div class="abs indicators">
      <svg width="22" height="22" viewBox="0 0 22 22"><circle cx="11" cy="11" r="10" fill="#fff"/><path d="M11 5v6h5" stroke="#000" stroke-width="2.5" fill="none"/></svg>
      <svg width="40" height="22" viewBox="0 0 40 22"><rect x="1" y="2" width="34" height="18" rx="3" fill="none" stroke="#fff" stroke-width="2"/><rect x="4" y="5" width="28" height="12" fill="#fff"/><rect x="36" y="8" width="3" height="6" fill="#fff"/></svg>
    </div>
  </div>

  <header class="abs app-header">
    <svg class="abs menu" width="44" height="34" viewBox="0 0 44 34"><rect y="0" width="44" height="6" rx="2" fill="#fff"/><rect y="14" width="44" height="6" rx="2" fill="#fff"/><rect y="28" width="44" height="6" rx="2" fill="#fff"/></svg>
    <h1 class="abs">Welcome back, Daniel</h1>
  </header>

  <section class="abs profile">
    <div class="abs backdrop" role="img" aria-label="Photo of a glass office building facade"></div>
    <div class="abs avatar" role="img" aria-label="Profile photo of Daniel Maron"></div>
    <div class="abs name">Daniel Maron</div>
    <div class="abs location">
      <svg width="16" height="24" viewBox="0 0 16 24"><path d="M8 0C3.6 0 0 3.5 0 8c0 6 8 16 8 16s8-10 8-16c0-4.5-3.6-8-8-8z" fill="#111"/><circle cx="8" cy="8" r="3" fill="#fff"/></svg>
      <span>San Francisco, CA</span>
    </div>
    <div class="abs score">
      <span class="label">Score</span>
      <span class="value">650</span>
      <svg width="26" height="40" viewBox="0 0 26 40"><path d="M8 2h10v22h7L13 38 1 24h7z" fill="#e53935" stroke="#b02020" stroke-width="1"/></svg>
      <span class="delta">-18</span>
    </div>
  </section>

  <div class="abs stats">
    <div class="stat" style="width:210px;padding-left:30px">
      <div class="figure">34%<svg width="22" height="28" viewBox="0 0 22 28"><path d="M7 27V13H1L11 1l10 12h-6v14z" fill="var(--arrow-up)"/></svg>+4</div>
      <div class="caption" style="margin-left:4px">Completion</div>
    </div>
    <div class="stat" style="width:289px;padding-left:26px">
      <div class="figure">20<svg width="22" height="28" viewBox="0 0 22 28"><path d="M7 27V13H1L11 1l10 12h-6v14z" fill="var(--arrow-up)"/></svg>+3<span style="margin-left:32px">18</span><svg width="22" height="28" viewBox="0 0 22 28"><path d="M7 27V13H1L11 1l10 12h-6v14z" fill="var(--arrow-up)"/></svg>+10</div>
      <div class="caption">Sessions<span style="margin-left:38px">Min.</span></div>
    </div>
    <div class="stat this-week" style="width:141px">This week</div>
  </div>
  <div class="abs progress"></div>
  <div class="abs progress-rest"></div>

  <div class="abs shortcut analytics">Analytics<svg width="26" height="14" viewBox="0 0 26 14"><path d="M2 12L13 3l11 9" stroke="#fff" stroke-width="3" fill="none" opacity="0.75"/></svg></div>
  <div class="abs shortcut course">Course<br>Overview<svg width="26" height="14" viewBox="0 0 26 14"><path d="M2 12L13 3l11 9" stroke="#fff" stroke-width="3" fill="none" opacity="0.75"/></svg></div>
  <div class="abs shortcut countdown">Days until<br>test 33<svg width="26" height="14" viewBox="0 0 26 14"><path d="M2 12L13 3l11 9" stroke="#fff" stroke-width="3" fill="none" opacity="0.75"/></svg></div>

  <div class="abs divider" style="top:781px"></div>

  <div class="abs up-next">
    <svg class="abs" style="left:0;top:0" width="427" height="152" viewBox="0 0 427 152"><path d="M42 0h328a42 42 0 0 1 42 42v54q0 30 15 54q-30-10-50-18H42A42 42 0 0 1 0 90V42A42 42 0 0 1 42 0z" fill="var(--red)"/></svg>
    <div class="abs text">
      <div class="topic">Up Next: Sentence Correction</div>
      <div class="lesson">Lesson 4</div>
    </div>
  </div>

  <div class="abs divider" style="top:1004px"></div>

  <nav class="abs tab-bar">
    <div class="tab">
      <svg width="66" height="48" viewBox="0 0 66 48" fill="#555"><rect x="4" y="2" width="52" height="7" rx="2"/><rect x="8" y="12" width="56" height="7" rx="2"/><rect x="2" y="22" width="52" height="7" rx="2"/><rect x="6" y="32" width="56" height="7" rx="2"/><rect x="2" y="41" width="54" height="7" rx="2"/></svg>
      <span>Theory</span>
    </div>
    <div class="tab">
      <svg width="46" height="54" viewBox="0 0 46 54"><rect x="3" y="6" width="40" height="46" rx="3" fill="none" stroke="#555" stroke-width="3"/><rect x="15" y="1" width="16" height="9" rx="2" fill="#555"/><g stroke="#555" stroke-width="2.5"><line x1="10" y1="20" x2="36" y2="20"/><line x1="10" y1="27" x2="36" y2="27"/><line x1="10" y1="34" x2="36" y2="34"/><line x1="10" y1="41" x2="36" y2="41"/></g></svg>
      <span>Practice</span>
    </div>
    <div class="tab active">
      <svg width="54" height="48" viewBox="0 0 54 48"><path d="M27 2L1 24h7v22h14V32h10v14h14V24h7L42 13V4h-6v4z" fill="#fff"/></svg>
      <span>Home</span>
    </div>
    <div class="tab">
      <svg width="54" height="36" viewBox="0 0 54 36"><path d="M14 2h26c8 0 12 6 13 16s-2 16-7 16-8-7-12-7H20c-4 0-7 7-12 7S0 28 1 18 6 2 14 2z" fill="#555"/><g fill="#fff"><rect x="11" y="14" width="12" height="4"/><rect x="15" y="10" width="4" height="12"/><circle cx="37" cy="12" r="2.5"/><circle cx="43" cy="17" r="2.5"/><circle cx="37" cy="21" r="2.5"/></g></svg>
      <span>Games</span>
    </div>
    <div class="tab">
      <svg width="48" height="52" viewBox="0 0 48 52"><rect x="2" y="6" width="38" height="44" fill="none" stroke="#555" stroke-width="3"/><g stroke="#555" stroke-width="2.5"><line x1="8" y1="18" x2="34" y2="18"/><line x1="8" y1="25" x2="34" y2="25"/><line x1="8" y1="32" x2="34" y2="32"/><line x1="8" y1="39" x2="34" y2="39"/></g><path d="M28 8l6 6 12-13" stroke="#555" stroke-width="4" fill="none"/></svg>
      <span>Test</span>
    </div>
  </nav>

</div>
</body>
</html>
```